Inspection Company - Commercial Brochure Design

We are looking to finalize our 8 x 11 brochure. We are an industry leader in our space of commercial and home inspections.

We really like the front and back design labeled-

We have made some suggestions for the internal pages-

These are only suggestions for the interior section- The wording should remain the same. The images can be removed / rearranged/ etc. There is full creative freedom for the interior.

Wording for Inside Right Page-
With over 500,000 properties inspected we know how to inspect each building type to maximize a Return On Investment for our clients. . Our Inspectors focus on all the critical building components (structural, roof, electrical, plumbing, air and heating, drainage, etc.), health and safety issues – emergency egress and other potential hazards. We document current condition and any immediate and future repairs that are necessary. When scheduling our team take all details into account building construction type, age, location, and property use into consideration to ensure we are fully prepared to conduct a thorough inspection.

Target Market(s)

Investors- Commercial Real Estate Investors

Industry/Entity Type

Commercial Real Estate Inspections

Requirements
Must have
• Similar branding to our website (https://morvanteq.com/brightcommercial) (https://bravuraassessments.com/) and ( the uploaded documents (Commercial report cover sample.JPG & designcrowd_z6se15j73jk0fe9fc2samkecn7_image (1).jpg )
Nice to have
• Must have Brand Logos and Brand Colors- Nice to have creative ideas of displaying the information

```html
<!DOCTYPE html>
<html lang="en">
<head>
<meta charset="utf-8">
<title>Northmark Group – Commercial Inspection Brochure</title>
<link rel="stylesheet" href="https://fonts.googleapis.com/css2?family=Roboto:wght@300;400;500;700;900&display=swap">
<style>
  :root {
    --stage: #8e8e8e;
    --brand-blue: #2a74c4;
    --brand-blue-deep: #1a5aa6;
    --brand-blue-bright: #2f8ae0;
    --ink: #262626;
    --ink-soft: #3a3a3a;
    --paper: #f4f4f4;
    --panel-dark: #2a2a2a;
    --panel-dark-2: #353535;
    --white: #ffffff;
  }
  * { box-sizing: border-box; margin: 0; padding: 0; }
  html, body { width: 1200px; height: 2232px; overflow: hidden; }
  body { background: var(--stage); font-family: "Roboto", sans-serif; color: var(--ink); position: relative; }

  .page-label { position: absolute; top: 255px; width: 548px; text-align: center; color: var(--white); font-weight: 300; font-size: 22px; }
  .page-label--cover { left: 41px; }
  .page-label--back { left: 611px; }

  .cover-page, .back-page { position: absolute; top: 300px; width: 548px; height: 733px; box-shadow: 0 4px 12px rgba(0,0,0,.35); }
  .cover-page { left: 41px; }
  .back-page { left: 611px; }
  .cover-page svg, .back-page svg { display: block; }

  .spread { position: absolute; left: 41px; top: 1110px; width: 1118px; height: 815px; background: var(--paper); box-shadow: 0 4px 12px rgba(0,0,0,.35); overflow: hidden; font-size: 13.5px; line-height: 17px; }
  .spread > * { position: absolute; }

  .section-tab { height: 40px; background: var(--brand-blue); color: var(--white); font-weight: 700; font-size: 16.5px; display: flex; align-items: center; padding-left: 20px; clip-path: polygon(0 0, calc(100% - 24px) 0, 100% 100%, 0 100%); }
  .body-copy { text-align: justify; color: var(--ink-soft); }

  .cert { left: 18px; width: 500px; display: flex; gap: 12px; font-size: 13.5px; line-height: 19px; color: var(--ink-soft); text-align: justify; }
  .cert-seal { flex: 0 0 46px; height: 46px; border-radius: 50%; margin-top: 2px; }
  .cert strong { color: var(--ink); }

  .properties-panel { left: 0; top: 513px; width: 305px; height: 302px; background: var(--brand-blue); color: var(--white); }
  .properties-panel::after { content: ""; position: absolute; right: -20px; top: 0; width: 20px; height: 18px; background: var(--brand-blue); clip-path: polygon(0 0, 0 100%, 100% 100%); }
  .properties-title { position: absolute; left: 42px; top: 37px; font-size: 16px; line-height: 18px; font-weight: 500; }
  .properties-list { position: absolute; left: 12px; top: 96px; width: 290px; list-style: none; display: grid; grid-template-columns: 155px 135px; row-gap: 7px; font-size: 13.5px; }
  .properties-list li { display: flex; align-items: center; gap: 10px; }
  .mini-icon { width: 11px; height: 11px; border: 2px solid var(--white); border-radius: 2px; }

  .report-panel { left: 305px; top: 530px; width: 225px; height: 285px; background: var(--panel-dark-2); color: var(--white); }
  .report-title { position: absolute; left: 20px; top: 60px; font-size: 12px; line-height: 14px; font-weight: 700; }
  .report-phone { position: absolute; left: 22px; top: 102px; width: 55px; height: 113px; border-radius: 8px; background: #111; border: 2px solid #555; }
  .report-phone .screen { position: absolute; inset: 10px 4px; background: linear-gradient(#dfe6ef, #6b86a8); }
  .report-sheet { position: absolute; left: 100px; top: 102px; width: 92px; height: 113px; background: linear-gradient(#e9eef5, #9fb2c9); border: 2px solid var(--white); }

  .services-panel { left: 530px; top: 530px; width: 588px; height: 285px; background: var(--panel-dark); color: var(--white); }
  .services-title { position: absolute; left: 37px; top: 25px; font-size: 17.5px; font-weight: 500; letter-spacing: .3px; white-space: nowrap; }
  .services-rule { position: absolute; left: 345px; top: 37px; width: 243px; height: 1px; background: #bdbdbd; }
  .services-list { position: absolute; left: 37px; top: 58px; list-style: none; font-size: 12.5px; }
  .services-list li { display: flex; align-items: center; gap: 8px; height: 27px; }
  .tick { width: 14px; height: 14px; }
  .tools-tab { position: absolute; left: 374px; top: 188px; width: 126px; height: 22px; background: var(--white); color: var(--ink); font-size: 12px; font-weight: 700; display: flex; justify-content: center; align-items: center; clip-path: polygon(10px 0, calc(100% - 10px) 0, 100% 100%, 0 100%); }
  .tools-bar { position: absolute; left: 57px; top: 208px; width: 486px; height: 62px; background: var(--white); border-radius: 31px; display: flex; align-items: center; justify-content: space-evenly; padding: 0 40px; }
  .tool-photo { width: 40px; height: 44px; border-radius: 8px; background: linear-gradient(#c9c9c9, #5b5b5b); }

  .inspect-photo { border-radius: 50%; border: 5px solid #e3e3e3; box-shadow: 0 2px 5px rgba(0,0,0,.35); }
  .inspect-photo--large { width: 125px; height: 125px; }
  .inspect-photo--small { width: 98px; height: 98px; }
  .component-label { font-size: 13.5px; line-height: 16px; color: var(--ink); }
  .component-label b { display: block; color: var(--brand-blue-bright); font-weight: 500; }
</style>
</head>
<body>

<div class="page-label page-label--cover">Cover Page</div>
<div class="page-label page-label--back">Back Page</div>

<div class="cover-page">
  <svg width="548" height="733" viewBox="0 0 548 733">
    <defs>
      <linearGradient id="paper-cover" x1="0" y1="0" x2="1" y2="1">
        <stop offset="0" stop-color="#f7f7f7"/><stop offset="1" stop-color="#d9d9d9"/>
      </linearGradient>
      <linearGradient id="facade-cover" x1="0" y1="0" x2="1" y2="1">
        <stop offset="0" stop-color="#0d4b9a"/><stop offset=".45" stop-color="#3c97d6"/><stop offset="1" stop-color="#12549f"/>
      </linearGradient>
    </defs>
    <rect width="548" height="733" fill="url(#paper-cover)"/>
    <polygon role="img" aria-label="Photo: glass skyscraper facade seen from below" points="0,0 140,0 548,620 548,733 0,733" fill="url(#facade-cover)"/>
    <polygon points="140,0 154,0 548,596 548,620" fill="#2f8ae0"/>
    <polygon points="0,425 0,460 320,733 365,733" fill="#2a86d8" opacity=".85"/>
    <circle cx="438" cy="120" r="55" fill="none" stroke="#2a6fb8" stroke-width="9"/>
    <text x="525" y="212" text-anchor="end" font-family="Roboto, sans-serif" font-weight="900" font-size="25" fill="#2a6fb8">NORTHMARK GROUP</text>
    <text x="525" y="280" text-anchor="end" font-family="Roboto, sans-serif" font-weight="900" font-size="24" fill="#1f6fc0">CALIFORNIA'S #1</text>
    <text x="525" y="303" text-anchor="end" font-family="Roboto, sans-serif" font-weight="700" font-size="17" fill="#1f6fc0">INSPECTION COMPANY</text>
    <text x="18" y="700" font-family="Roboto, sans-serif" font-weight="700" font-size="13" letter-spacing="1.5" fill="#ffffff">WWW.NORTHMARKINSPECT.COM</text>
  </svg>
</div>

<div class="back-page">
  <svg width="548" height="733" viewBox="0 0 548 733">
    <defs>
      <linearGradient id="paper-back" x1="0" y1="0" x2="1" y2="1">
        <stop offset="0" stop-color="#f7f7f7"/><stop offset="1" stop-color="#d9d9d9"/>
      </linearGradient>
      <linearGradient id="facade-back" x1="1" y1="0" x2="0" y2="1">
        <stop offset="0" stop-color="#0d4b9a"/><stop offset=".45" stop-color="#3c97d6"/><stop offset="1" stop-color="#12549f"/>
      </linearGradient>
    </defs>
    <rect width="548" height="733" fill="url(#paper-back)"/>
    <polygon points="200,0 375,110 455,0" fill="#c9c9c9" opacity=".6"/>
    <polyline points="185,0 375,125 470,0" fill="none" stroke="#2a7fd4" stroke-width="14"/>
    <polygon role="img" aria-label="Photo: glass skyscraper facade seen from below" points="470,0 548,0 548,733 0,733 0,660" fill="url(#facade-back)"/>
    <polygon points="470,0 486,0 0,680 0,655" fill="#2f8ae0"/>
    <polygon points="548,465 548,500 345,733 300,733" fill="#2a86d8" opacity=".85"/>
    <text x="22" y="100" font-family="Roboto, sans-serif" font-weight="700" font-size="21" fill="#262626">CONTACT US</text>
    <text x="22" y="130" font-family="Roboto, sans-serif" font-weight="700" font-size="20" fill="#2a7fd4">HEAD OFFICE</text>
    <text font-family="Roboto, sans-serif" font-weight="500" font-size="14" fill="#2f2f2f">
      <tspan x="22" y="163">2150 LARKMONT AVE STE 410, WESTBROOK</tspan>
      <tspan x="22" y="179">HILLS, CA 91802</tspan>
      <tspan x="22" y="204">+1 800-555-0142</tspan>
      <tspan x="22" y="228">service@northmarkinspect.com</tspan>
    </text>
    <rect x="16" y="245" width="212" height="47" rx="6" fill="#2a6fb8"/>
  </svg>
</div>

<div class="spread">
  <div class="section-tab" style="left:0;top:15px;width:375px;">OUR EXPERTISE = YOUR PEACE OF MIND</div>
  <p class="body-copy" style="left:20px;top:70px;width:498px;">Our clients appreciate the clear and high quality information that we provide, which helps in negotiations and understanding the overall condition of the commercial property. Commercial real estate is a big investment and its highly advised you make an initial investment in an inspection with a Certified Team of Experts before finalizing a transaction.&nbsp; Trust our team of experts who are Certified with the industries highest accolades.</p>

  <div class="section-tab" style="left:0;top:178px;width:425px;">OUR COMMERCIAL INSPECTORS ARE CERTIFIED</div>
  <div class="cert" style="top:232px;"><span class="cert-seal" style="background:#c8302c;"></span><p><strong>CPIG-</strong> Commercial Property Inspectors Guild -Highest degree of training and standards adhering to the International Standards of Practice forInspecting Commercial Properties (CPSOP).</p></div>
  <div class="cert" style="top:308px;"><span class="cert-seal" style="background:#c9a437;"></span><p><strong>WIBA-</strong> Worlds largest Certifying body for the inspection industry. Worldwide Inspectors Board of Accreditation.</p></div>
  <div class="cert" style="top:366px;"><span class="cert-seal" style="background:#5a5a5a;"></span><p><strong>P.R.A-</strong> Pacific Realty Alliance Certified Inspectors.Verified Association Credentials, Background checks, and verified Insurance Documents.</p></div>
  <p class="body-copy" style="left:22px;top:448px;width:496px;font-size:13.5px;line-height:19px;">All this to ensure your getting the most thorough commercial inspection available.</p>

  <div class="properties-panel">
    <div class="properties-title">COMMERCIAL PROPERTIES<br>WE INSPECT</div>
    <ul class="properties-list">
      <li><span class="mini-icon"></span>Apartments</li><li><span class="mini-icon"></span>Churches</li>
      <li><span class="mini-icon"></span>Strip Centers</li><li><span class="mini-icon"></span>Retail</li>
      <li><span class="mini-icon"></span>Hotels/Motels</li><li><span class="mini-icon"></span>Leases</li>
      <li><span class="mini-icon"></span>Hospitals</li><li><span class="mini-icon"></span>Warehouses</li>
      <li><span class="mini-icon"></span>Day Cares</li><li><span class="mini-icon"></span>Industrial</li>
      <li><span class="mini-icon"></span>Multi-Family</li><li><span class="mini-icon"></span>Restaurants</li>
    </ul>
  </div>

  <div class="report-panel">
    <div class="report-title">EASY TO UNDERSTAND &amp;<br>READ DIGITAL PHOTO REPORT</div>
    <div class="report-phone"><div class="screen" role="img" aria-label="Digital inspection report shown on a phone"></div></div>
    <div class="report-sheet" role="img" aria-label="Sample page of a digital photo inspection report"></div>
  </div>

  <div class="section-tab" style="left:545px;top:15px;width:235px;">WHAT WE INSPECT</div>
  <p class="body-copy" style="left:546px;top:72px;width:552px;">With over 500,000 properties inspected we know how to inspect each building type to maximize a Return On Investment for our clients. . Our Inspectors focus on all the critical building components (structural, roof, electrical, plumbing, air and heating, drainage, etc.), health and safety issues – emergency egress and other potential hazards. We document current conditions and any immediate and future repairs that are necessary. When scheduling our team takes all details into account building construction type, age, location, and property use into consideration to ensure we are fully prepared to conduct a thorough inspection.</p>

  <div class="section-tab" style="left:545px;top:222px;width:400px;">CONCRETE, STEEL AND WOOD COMPONENTS</div>

  <div class="inspect-photo inspect-photo--large" style="left:550px;top:270px;background:linear-gradient(135deg,#d9d4cc,#4a4a52);" role="img" aria-label="Photo: inspector checking an electrical panel"></div>
  <div class="inspect-photo inspect-photo--small" style="left:625px;top:348px;background:linear-gradient(135deg,#e8e3dc,#c9a13a);" role="img" aria-label="Photo: outlet tester in use"></div>
  <div class="inspect-photo inspect-photo--large" style="left:730px;top:270px;background:linear-gradient(135deg,#cfd6df,#55606e);" role="img" aria-label="Photo: inspector examining a roof"></div>
  <div class="inspect-photo inspect-photo--small" style="left:805px;top:348px;background:linear-gradient(135deg,#d8e4f0,#4c6e96);" role="img" aria-label="Photo: inspector checking a window"></div>
  <div class="inspect-photo inspect-photo--large" style="left:915px;top:270px;background:linear-gradient(135deg,#d6d3cf,#3f3f44);" role="img" aria-label="Photo: thermal camera check at a foundation"></div>
  <div class="inspect-photo inspect-photo--small" style="left:990px;top:348px;background:linear-gradient(135deg,#dcdcd8,#6f7a64);" role="img" aria-label="Photo: inspector checking for moisture"></div>

  <p class="component-label" style="left:566px;top:452px;"><b>PLUMBING</b>Panel, Outlets, Wiring</p>
  <p class="component-label" style="left:740px;top:452px;"><b>ROOF</b>Drainage, Grade, Moisture<br>concrete, steel &amp; wood<br>components Entry</p>
  <p class="component-label" style="left:932px;top:452px;"><b>FOUNDATION</b>Leaks, Type, Moisture<br>Intrustion</p>

  <div class="services-panel">
    <div class="services-title">ADDITIONAL SERVICES&nbsp; AVAILABLE</div>
    <div class="services-rule"></div>
    <ul class="services-list">
      <li><svg class="tick" viewBox="0 0 14 14"><circle cx="7" cy="7" r="7" fill="#2a74c4"/><path d="M3.5 7.2l2.3 2.3 4.7-4.8" fill="none" stroke="#fff" stroke-width="1.6"/></svg>ADA COMPLIANCE INSPECTIONS</li>
      <li><svg class="tick" viewBox="0 0 14 14"><circle cx="7" cy="7" r="7" fill="#2a74c4"/><path d="M3.5 7.2l2.3 2.3 4.7-4.8" fill="none" stroke="#fff" stroke-width="1.6"/></svg>ROOF CERTIFICATION AND MAINTENANCE - LICENSED ROOFER</li>
      <li><svg class="tick" viewBox="0 0 14 14"><circle cx="7" cy="7" r="7" fill="#2a74c4"/><path d="M3.5 7.2l2.3 2.3 4.7-4.8" fill="none" stroke="#fff" stroke-width="1.6"/></svg>MOLD AND MOISTURE ANALYSIS FROM CERTIFIED MOLD EXPERT</li>
      <li><svg class="tick" viewBox="0 0 14 14"><circle cx="7" cy="7" r="7" fill="#2a74c4"/><path d="M3.5 7.2l2.3 2.3 4.7-4.8" fill="none" stroke="#fff" stroke-width="1.6"/></svg>SEWER CAMERA INSPECTIONS</li>
      <li><svg class="tick" viewBox="0 0 14 14"><circle cx="7" cy="7" r="7" fill="#2a74c4"/><path d="M3.5 7.2l2.3 2.3 4.7-4.8" fill="none" stroke="#fff" stroke-width="1.6"/></svg>TERMITE INSPECTIONS</li>
    </ul>
    <div class="tools-tab">TOOLS WE USE</div>
    <div class="tools-bar">
      <span class="tool-photo" role="img" aria-label="Photo: inspection tool"></span>
      <span class="tool-photo" role="img" aria-label="Photo: moisture meter"></span>
      <span class="tool-photo" role="img" aria-label="Photo: sewer camera reel"></span>
      <span class="tool-photo" role="img" aria-label="Photo: inspection drone"></span>
      <span class="tool-photo" role="img" aria-label="Photo: voltage tester"></span>
      <span class="tool-photo" role="img" aria-label="Photo: thermal imaging camera"></span>
    </div>
  </div>
</div>

</body>
</html>
```